Irrigation Business needs their business cards modernised and revamped

I would like to keep my current logo, colours and revamp the format of the card.

I would like the card to be clean yet important.

Im not sure if you include texture but i would like the named logo to be indented into the card etc.

show me something alive and free something thats clinical to the point yet has a feel of achievement. i would like people to go nice card.

Target Market(s)

high end clients, corporate, sports field manger, the guys that make the decisions

Industry/Entity Type

Business

Contact Information for Business Card

nformation to be included

Dean Harlow (Director)
0487305526
dean@kolvat.biz
www.kestonfieldworks.com

instagram logo
google logo
facebook logo

Colors

Designer to choose colors to be used in the design.

Requirements
Nice to have
• indentations a really nice feel to the card good texture

```html
<!DOCTYPE html>
<html lang="en">
<head>
<meta charset="utf-8">
<title>Keston Fieldworks – Business Cards</title>
<link rel="stylesheet" href="https://fonts.googleapis.com/css2?family=Roboto:wght@400;700&display=swap">
<style>
  :root {
    --backdrop: #e6e6e6;
    --card: #f4f4f5;
    --brand-blue: #2f5597;
    --brand-sky: #3a8fc6;
    --brand-faint: #e6e9ee;
    --ink: #333a45;
    --shadow: rgba(0,0,0,0.22);
  }
  html, body {
    margin: 0;
    padding: 0;
    width: 1200px;
    height: 576px;
    overflow: hidden;
    background: var(--backdrop);
    font-family: "Roboto", Arial, sans-serif;
  }
  .stage { position: relative; width: 1200px; height: 576px; }
  .card {
    position: absolute;
    top: 138px;
    height: 294px;
    background: var(--card);
    border-radius: 12px;
    box-shadow: 0 4px 8px var(--shadow);
    overflow: hidden;
  }
  .card--front { left: 82px; width: 485px; }
  .card--back  { left: 602px; width: 481px; }

  .faint-mark {
    position: absolute;
    left: 290px; top: 10px;
    width: 200px; height: 200px;
    border-radius: 50%;
    background: var(--brand-faint);
    opacity: 0.7;
  }
  .brand-disc {
    position: absolute;
    left: 196px; top: 56px;
    width: 92px; height: 92px;
    border-radius: 50%;
    background: var(--brand-blue);
  }
  .brand-name {
    margin: 0;
    color: var(--brand-blue);
    font-weight: 700;
    text-transform: uppercase;
    letter-spacing: -0.5px;
    white-space: nowrap;
  }
  .card--front .brand-name {
    position: absolute;
    left: 0; right: 0; top: 158px;
    text-align: center;
    font-size: 29px;
  }
  .social-rule {
    position: absolute;
    left: 0; right: 0; top: 264px;
    display: flex; align-items: center; justify-content: center; gap: 6px;
  }
  .social-rule .rule { width: 120px; height: 2px; background: var(--brand-blue); }
  .social-rule .rule:first-child { margin-right: 12px; }
  .social-rule .rule:last-child { margin-left: 12px; }
  .social-dot {
    width: 16px; height: 16px; border-radius: 50%;
    background: var(--brand-blue);
  }
  .social-dot--sky { background: var(--brand-sky); }

  .card--back .brand-name {
    position: absolute; left: 24px; top: 30px;
    font-size: 28px;
  }
  .person { position: absolute; left: 24px; top: 138px; }
  .person__name {
    margin: 0; font-size: 20px; font-weight: 700;
    color: var(--brand-blue); text-transform: uppercase;
  }
  .person__role { margin: 3px 0 0; font-size: 11.5px; color: var(--ink); }
  .socials { position: absolute; left: 24px; top: 196px; display: flex; gap: 4px; }
  .contacts {
    position: absolute; left: 24px; top: 220px;
    margin: 0; padding: 0; list-style: none;
    font-size: 12.5px; color: var(--ink);
  }
  .contacts li { display: flex; align-items: center; height: 16.5px; }
  .contacts svg { width: 10px; height: 10px; margin-right: 14px; fill: var(--brand-blue); }
  .big-disc {
    position: absolute;
    left: 274px; top: 38px;
    width: 216px; height: 216px;
    border-radius: 50%;
    background: var(--brand-blue);
  }
</style>
</head>
<body>
<main class="stage">
  <section class="card card--front" aria-label="Card front">
    <div class="faint-mark" aria-hidden="true"></div>
    <div class="brand-disc" aria-hidden="true"></div>
    <h1 class="brand-name">Keston Fieldworks</h1>
    <div class="social-rule" aria-label="Social media">
      <span class="rule"></span>
      <span class="social-dot"></span>
      <span class="social-dot social-dot--sky"></span>
      <span class="social-dot"></span>
      <span class="rule"></span>
    </div>
  </section>

  <section class="card card--back" aria-label="Card back">
    <h2 class="brand-name">Keston Fieldworks</h2>
    <div class="person">
      <p class="person__name">Dean Harlow</p>
      <p class="person__role">Director</p>
    </div>
    <div class="socials" aria-label="Social media">
      <span class="social-dot"></span>
      <span class="social-dot social-dot--sky"></span>
      <span class="social-dot"></span>
    </div>
    <ul class="contacts">
      <li><svg viewBox="0 0 10 10" aria-hidden="true"><path d="M1 3 Q5 0 9 3 L8 4.5 L6.5 3.8 L6.5 3 Q5 2.5 3.5 3 L3.5 3.8 L2 4.5 Z M2 6 H8 V9 H2 Z"/></svg>0487305526</li>
      <li><svg viewBox="0 0 10 10" aria-hidden="true"><path d="M0.5 2 H9.5 V8 H0.5 Z M1 2.5 L5 5.5 L9 2.5" stroke="#f4f4f5" stroke-width="0.8"/></svg>dean@kolvat.biz</li>
      <li><svg viewBox="0 0 10 10" aria-hidden="true"><circle cx="5" cy="5" r="4.5"/><path d="M0.5 5 H9.5 M5 0.5 V9.5" stroke="#f4f4f5" stroke-width="0.8"/></svg>www.kestonfieldworks.com</li>
    </ul>
    <div class="big-disc" aria-hidden="true"></div>
  </section>
</main>
</body>
</html>
```